BLS Business Card 2018

Larkmere Chiropractic. We have two locations that we want to advertise on the same card. Brightvale OrthoCore campus address: 3815 Pellham Dr., Suite 240, Flowood, MS 39417. Madison address: 246 Willowmere Dr., Building D., Madison, MS 39284. website: www.drlarkmere-example.com. o:(601)555-0147 f:(601)555-0183

Target Market(s)

Health care decision makers: primary care doctors and mothers

Contact Information for Business Card

I have no idea; up for any suggestions and I'd do much better picking from examples versus describing what I'm looking for. We are in a very high end location and would like the cards to look really sharp.

Requirements
Must have
• My name, Martin R Belvane, D.C.

```html
<!DOCTYPE html>
<html lang="en">
<head>
<meta charset="utf-8">
<title>Larkmere Chiropractic – Business Card</title>
<link rel="stylesheet" href="https://fonts.googleapis.com/css2?family=Open+Sans:wght@300;400;700&family=Open+Sans+Condensed:wght@700&display=swap">
<style>
  :root {
    --page-bg: #e9e6e1;
    --card-white: #f7f7f5;
    --ink: #1b1b1b;
    --ink-soft: #4a4a4a;
    --rule: #bdbdbd;
    --band-black: #111111;
    --band-grey: #3a3a3a;
    --band-text: #e6e6e6;
    --back-black: #050505;
    --sketch-tone: #2a2a2a;
  }
  * { box-sizing: border-box; margin: 0; padding: 0; }
  html, body { width: 1200px; height: 950px; overflow: hidden; }
  body {
    background: var(--page-bg);
    font-family: "Open Sans", Arial, sans-serif;
    color: var(--ink);
    position: relative;
  }
  .card {
    position: absolute;
    left: 270px;
    width: 660px;
    height: 377px;
    box-shadow: 0 6px 18px rgba(0,0,0,0.18);
    overflow: hidden;
  }
  .card-front { top: 70px; background: var(--card-white); }
  .card-back { top: 503px; background: var(--back-black); }

  .brand {
    position: absolute;
    left: 60px;
    top: 140px;
    display: flex;
    align-items: center;
    gap: 14px;
  }
  .brand-dot {
    width: 34px; height: 34px;
    border-radius: 50%;
    background: var(--ink-soft);
    flex: none;
  }
  .brand-name {
    font-weight: 300;
    font-size: 22px;
    line-height: 1.15;
    letter-spacing: 2px;
    text-transform: uppercase;
    color: var(--ink-soft);
  }

  .divider {
    position: absolute;
    left: 312px;
    top: 40px;
    width: 1px;
    height: 240px;
    background: linear-gradient(to bottom, transparent, var(--rule) 20%, var(--rule) 80%, transparent);
  }

  .contact {
    position: absolute;
    left: 340px;
    top: 44px;
    width: 300px;
  }
  .contact-name {
    font-family: "Open Sans Condensed", "Open Sans", sans-serif;
    font-weight: 700;
    font-size: 21px;
    color: var(--ink);
    margin-bottom: 8px;
  }
  .contact-line {
    font-weight: 400;
    font-size: 13px;
    line-height: 1.6;
    color: var(--ink-soft);
  }
  .contact-phones { margin-top: 6px; }

  .band {
    position: absolute;
    left: 0; right: 0;
    bottom: 18px;
    height: 44px;
    background: linear-gradient(to right, var(--band-grey), var(--band-black) 40%);
    display: flex;
    align-items: center;
    justify-content: flex-end;
    padding-right: 40px;
  }
  .band::after {
    content: "";
    position: absolute;
    left: 0; right: 0;
    top: -6px;
    height: 2px;
    background: var(--band-black);
  }
  .band-web {
    font-size: 13px;
    letter-spacing: 5px;
    text-transform: uppercase;
    color: var(--band-text);
  }

  .back-sketch {
    position: absolute;
    left: 150px;
    top: 100px;
    width: 360px;
    height: 170px;
    border-radius: 40px;
    background: radial-gradient(ellipse at center, var(--sketch-tone), var(--back-black) 75%);
  }
</style>
</head>
<body>
  <section class="card card-front" aria-label="Business card front">
    <div class="brand">
      <span class="brand-dot"></span>
      <span class="brand-name">Larkmere<br>Chiropractic</span>
    </div>
    <div class="divider"></div>
    <div class="contact">
      <p class="contact-name">MARTIN R BELVANE, D.C.</p>
      <p class="contact-line">Brightvale OrthoCore campus :</p>
      <p class="contact-line">3815 Pellham Dr., Suite 240</p>
      <p class="contact-line">Flowood, MS 39417.</p>
      <p class="contact-line">Madison address:</p>
      <p class="contact-line">246 Willowmere Dr., Building D.</p>
      <p class="contact-line">Madison, MS 39284.</p>
      <p class="contact-line contact-phones">P. (601)555-0147 M. (601)555-0183</p>
    </div>
    <div class="band">
      <span class="band-web">www.drlarkmere-example.com</span>
    </div>
  </section>

  <section class="card card-back" aria-label="Business card back">
    <div class="back-sketch" role="img" aria-label="White line sketch of a patient lying face down receiving a spinal adjustment"></div>
  </section>
</body>
</html>
```